Structural Engineering Business Card

Brookvane Drafting does residential house plans for clients in Central Florida. Would like simple but elegant business card that is appropriate for a house plan engineering company. Prefer black business card with black/white them but open to other shades of blue. I uploaded a sample card that I came across that looked good but please come up with your own creative designs.

Contact Information for Business Card

Name, Title, Phone, Email, Address, website

```html
<!DOCTYPE html>
<html lang="en">
<head>
<meta charset="utf-8">
<title>Brookvane Drafting — Business Card</title>
<link href="https://fonts.googleapis.com/css2?family=Nunito+Sans:wght@300;400;700;800&display=swap" rel="stylesheet">
<style>
  :root {
    --stage: #d9d9d9;
    --card-light: #ffffff;
    --card-dark: #0b0b0b;
    --ink-dark: #111111;
    --ink-light: #f2f2f2;
    --accent: #5bb8e6;
    --divider: #8a8a8a;
  }
  * { margin: 0; padding: 0; box-sizing: border-box; }
  html, body {
    width: 1200px; height: 900px; overflow: hidden;
    background: var(--stage);
    font-family: "Nunito Sans", sans-serif;
  }
  .canvas { position: relative; width: 1200px; height: 900px; }

  .card {
    position: absolute;
    width: 600px; height: 343px;
    border-radius: 26px;
    box-shadow: 0 10px 28px rgba(0,0,0,0.25);
    overflow: hidden;
  }
  .card--front { left: 90px; top: 90px; background: var(--card-light); color: var(--ink-dark); }
  .card--back { left: 510px; top: 467px; background: var(--card-dark); color: var(--ink-light); }

  /* front */
  .front-brand {
    position: absolute; left: 0; right: 0; top: 122px;
    text-align: center;
  }
  .front-brand .site {
    font-size: 15px; font-weight: 400; letter-spacing: 0.5px;
    margin-bottom: 4px;
  }
  .wordmark {
    display: inline-flex; align-items: center; gap: 12px;
    font-weight: 800; text-transform: uppercase; letter-spacing: 0.5px;
    line-height: 1;
  }
  .wordmark .mark-square { width: 22px; height: 22px; background: currentColor; }
  .front-brand .wordmark { font-size: 40px; }

  /* back */
  .back-brand { position: absolute; left: 34px; top: 44px; }
  .back-brand .wordmark { font-size: 34px; color: var(--ink-light); }

  .person {
    position: absolute; right: 318px; top: 210px;
    text-align: right;
  }
  .person .name {
    color: var(--accent); font-weight: 700; font-size: 20px;
    letter-spacing: 0.5px; text-transform: uppercase;
  }
  .person .title { font-weight: 300; font-size: 18px; margin-top: 2px; }

  .divider {
    position: absolute; left: 298px; top: 190px;
    width: 1px; height: 112px; background: var(--divider);
  }

  .contacts {
    position: absolute; left: 314px; top: 190px;
    list-style: none;
  }
  .contacts li {
    display: flex; align-items: center; gap: 8px;
    font-size: 15px; font-weight: 400; height: 28px;
    white-space: nowrap;
  }
  .contacts svg { width: 15px; height: 15px; flex: none; fill: var(--accent); }
</style>
</head>
<body>
<main class="canvas">

  <section class="card card--front" aria-label="Business card front">
    <div class="front-brand">
      <p class="site">www.brookvanedrafting.com</p>
      <div class="wordmark"><span class="mark-square"></span>Brookvane Drafting</div>
    </div>
  </section>

  <section class="card card--back" aria-label="Business card back">
    <div class="back-brand">
      <div class="wordmark"><span class="mark-square"></span>Brookvane Drafting</div>
    </div>

    <div class="person">
      <p class="name">Dana Whitfield</p>
      <p class="title">Architectural Director</p>
    </div>

    <div class="divider"></div>

    <ul class="contacts">
      <li>
        <svg viewBox="0 0 24 24" aria-hidden="true"><path d="M6.6 10.8a15.1 15.1 0 0 0 6.6 6.6l2.2-2.2a1 1 0 0 1 1-.25 11.4 11.4 0 0 0 3.6.57 1 1 0 0 1 1 1V20a1 1 0 0 1-1 1A17 17 0 0 1 3 4a1 1 0 0 1 1-1h3.5a1 1 0 0 1 1 1c0 1.25.2 2.45.57 3.57a1 1 0 0 1-.25 1z"/></svg>
        555-014-2280
      </li>
      <li>
        <svg viewBox="0 0 24 24" aria-hidden="true"><path d="M3 5h18a1 1 0 0 1 1 1v12a1 1 0 0 1-1 1H3a1 1 0 0 1-1-1V6a1 1 0 0 1 1-1zm1 2.2V17h16V7.2l-8 5.3z"/></svg>
        info@brookvanedrafting.com
      </li>
      <li>
        <svg viewBox="0 0 24 24" aria-hidden="true"><path d="M12 2a10 10 0 1 0 0 20 10 10 0 0 0 0-20zm0 2c.9 0 2.2 1.8 2.8 5H9.2C9.8 5.8 11.1 4 12 4zM4.3 10h2.9a17 17 0 0 0 0 4H4.3a8 8 0 0 1 0-4zm4.9 0h5.6a15 15 0 0 1 0 4H9.2a15 15 0 0 1 0-4zm7.6 0h2.9a8 8 0 0 1 0 4h-2.9a17 17 0 0 0 0-4zM9.2 15h5.6c-.6 3.2-1.9 5-2.8 5s-2.2-1.8-2.8-5z"/></svg>
        www.brookvanedrafting.com
      </li>
      <li>
        <svg viewBox="0 0 24 24" aria-hidden="true"><path d="M12 2a7 7 0 0 0-7 7c0 5.2 7 13 7 13s7-7.8 7-13a7 7 0 0 0-7-7zm0 9.5A2.5 2.5 0 1 1 12 6.5a2.5 2.5 0 0 1 0 5z"/></svg>
        42 Palmetto Row, Ocala FL
      </li>
    </ul>
  </section>

</main>
</body>
</html>
```